New Dental Office Needs an Attractive and user friendly Website Designed

I need a website for a new dental office. The Name is Harrowfield Dentistry. I would like a Modern design with a user friendly interface and usability.
I would like a landing page, a page that lists the services we offer: Cosmetic Dentistry, Implants, Dental Hygiene, Emergency Services, Restorations, Dentures
Target Market(s)
Mid to upper class
Industry/Entity Type
Dentistry
Coding
Number of Pages Required
1 page
Requirements
Must have
- Landing page that has a scheduling option, Procedures, operating hours, and contact us info
Nice to have
- Appealing design, Soft comforting colors. Easy to navigate page, Modern and professional.

```html
<!DOCTYPE html>
<html lang="en">
<head>
<meta charset="utf-8">
<title>Harrowfield Dentistry</title>
<link href="https://fonts.googleapis.com/css2?family=Playfair+Display:wght@400;500;600&family=Lato:wght@400;700&family=Montserrat:wght@500;600&display=swap" rel="stylesheet">
<style>
:root{
  --ink:#1d1d1f;
  --navy:#2d3e50;
  --teal:#5bbfb5;
  --teal-soft:#e3f2f0;
  --blue:#1aa3e8;
  --gold:#d4a72c;
  --paper:#f5f7f9;
  --white:#ffffff;
  --muted:#6b7480;
  --footer:#232323;
}
*{margin:0;padding:0;box-sizing:border-box}
html,body{width:1200px;height:3450px;overflow:hidden}
body{position:relative;background:var(--white);font-family:'Lato',sans-serif;color:var(--ink)}
.abs{position:absolute}
.serif{font-family:'Playfair Display',serif}

/* header */
.site-header{position:absolute;left:0;top:0;width:1200px;height:91px;background:var(--white)}
.brand{position:absolute;left:141px;top:28px;font-family:'Playfair Display',serif;font-size:30px;font-weight:500;color:var(--ink)}
.nav a{position:absolute;top:37px;font-family:'Montserrat',sans-serif;font-size:13px;font-weight:500;color:var(--ink);text-decoration:none}
.nav a.active{color:var(--blue)}
.btn-book{position:absolute;display:flex;align-items:center;justify-content:center;gap:8px;background:var(--blue);color:var(--white);font-family:'Montserrat',sans-serif;font-weight:600;font-size:13px;border-radius:22px;text-decoration:none}
.btn-book svg{width:15px;height:15px}

/* hero */
.hero{position:absolute;left:0;top:91px;width:1200px;height:532px;background:linear-gradient(90deg,#f4f4f4 0%,#eeeeee 35%,#d9dcdf 55%,#c8cdd2 75%,#e6e8ea 100%)}
.hero-title{position:absolute;left:141px;top:95px;font-family:'Playfair Display',serif;font-size:54px;line-height:63px;font-weight:500;color:var(--ink);width:480px}
.hero-sub{position:absolute;left:139px;top:296px;font-family:'Montserrat',sans-serif;font-size:22px;line-height:32px;font-weight:500;color:var(--ink);width:490px}

/* section heads */
.section-title{position:absolute;left:0;width:1200px;text-align:center;font-family:'Playfair Display',serif;font-size:31px;font-weight:500}
.section-title span{position:relative}
.section-title span::after{content:"";position:absolute;left:0;right:0;bottom:-4px;height:2px;background:var(--gold)}
.section-lead{position:absolute;left:350px;width:500px;text-align:center;font-size:12.5px;line-height:16px;color:var(--muted)}

/* services */
.services{position:absolute;left:0;top:623px;width:1200px;height:626px;background:var(--paper)}
.service-card{position:absolute;width:291px;height:187px;background:var(--teal-soft);border-radius:16px}
.service-icon{position:absolute;left:21px;top:21px;width:41px;height:41px;background:var(--teal);border-radius:7px;display:flex;align-items:center;justify-content:center}
.service-icon svg{width:24px;height:24px;fill:none;stroke:var(--white);stroke-width:1.6;stroke-linecap:round;stroke-linejoin:round}
.service-card h3{position:absolute;left:21px;top:93px;font-family:'Playfair Display',serif;font-size:20px;font-weight:500;color:#2d3e50}
.service-card p{position:absolute;left:21px;top:121px;width:255px;font-size:12.5px;line-height:15.5px;color:#3b4450}

/* why */
.why{position:absolute;left:0;top:1249px;width:1200px;height:694px;background:var(--navy)}
.why .section-title{color:var(--white)}
.why .section-lead{color:#e6ebef}
.why-item{position:absolute;left:141px;width:423px;height:98px;background:#f4f6f8;border-radius:8px}
.why-icon{position:absolute;left:14px;top:14px;width:70px;height:70px;background:#e7ecef;border-radius:8px;display:flex;align-items:center;justify-content:center}
.why-icon svg{width:34px;height:34px;fill:var(--teal)}
.why-item h3{position:absolute;left:99px;top:15px;font-family:'Playfair Display',serif;font-size:21px;font-weight:500;color:var(--ink)}
.why-item p{position:absolute;left:99px;top:47px;width:310px;font-size:12.5px;line-height:15.5px;color:#7a8088}
.portrait-frame{position:absolute;left:610px;top:177px;width:458px;height:448px;border-radius:90px 0 110px 0;background:var(--teal)}
.portrait{position:absolute;left:600px;top:187px;width:458px;height:436px;border-radius:80px 0 100px 0;background:linear-gradient(135deg,#e8ebee 0%,#d2d8dd 50%,#bcc6cf 100%)}

/* visit */
.visit{position:absolute;left:0;top:1943px;width:1200px;height:719px;background:var(--paper)}
.map-area{position:absolute;left:141px;top:187px;width:642px;height:461px;background:linear-gradient(135deg,#eee9e0 0%,#d9e7f3 45%,#a8cdec 100%)}
.info-card{position:absolute;left:758px;top:256px;width:300px;height:324px;background:var(--navy);border-radius:12px;color:var(--white)}
.info-card h4{position:absolute;left:28px;font-family:'Playfair Display',serif;font-size:19px;font-weight:500;display:flex;align-items:center;gap:6px}
.info-card h4 svg{width:17px;height:17px;fill:none;stroke:var(--teal);stroke-width:1.8;stroke-linecap:round;stroke-linejoin:round}
.info-card p{position:absolute;left:28px;font-size:12.5px;line-height:15.5px}
.btn-call{position:absolute;left:28px;top:265px;width:92px;height:31px;background:var(--white);color:var(--ink);border-radius:4px;font-size:12.5px;display:flex;align-items:center;justify-content:center;text-decoration:none}

/* reviews */
.reviews{position:absolute;left:0;top:2662px;width:1200px;height:510px;background:var(--navy)}
.reviews .section-title{color:var(--white)}
.reviews .section-lead{color:#e6ebef}
.review-card{position:absolute;top:173px;width:448px;height:190px;background:#f6f7f8;border-radius:10px}
.stars{position:absolute;left:21px;top:21px;display:flex;gap:5px}
.stars svg{width:21px;height:21px;fill:var(--gold)}
.review-date{position:absolute;right:22px;top:26px;font-size:12.5px;color:var(--ink)}
.review-text{position:absolute;left:21px;top:66px;width:405px;font-size:12.5px;line-height:15.5px;color:var(--ink)}
.avatar{position:absolute;left:21px;top:125px;width:55px;height:55px;border-radius:50%;background:linear-gradient(135deg,#e5d2bf,#9c7a62)}
.reviewer{position:absolute;left:90px;top:131px;font-family:'Playfair Display',serif;font-size:20px;font-weight:500}
.role{position:absolute;left:90px;top:157px;font-size:12.5px;color:var(--muted)}
.arrow-btn{position:absolute;top:257px;width:29px;height:29px;border-radius:5px;display:flex;align-items:center;justify-content:center}
.arrow-btn svg{width:14px;height:14px;fill:none;stroke-width:2;stroke-linecap:round;stroke-linejoin:round}
.btn-view{position:absolute;left:546px;top:407px;width:106px;height:39px;background:var(--teal);color:var(--white);border-radius:4px;font-size:13px;display:flex;align-items:center;justify-content:center;text-decoration:none}

/* footer */
.site-footer{position:absolute;left:0;top:3172px;width:1200px;height:278px;background:var(--footer);color:var(--white)}
.footer-brand{position:absolute;left:0;width:1200px;top:56px;text-align:center;font-family:'Playfair Display',serif;font-size:26px;font-weight:500}
.footer-nav{position:absolute;left:0;width:1200px;top:126px;display:flex;justify-content:center;gap:29px;font-family:'Playfair Display',serif;font-size:13px}
.footer-nav a{color:var(--white);text-decoration:none}
.social{position:absolute;left:0;width:1200px;top:165px;display:flex;justify-content:center;gap:30px}
.social span{width:13px;height:13px;background:var(--white);border-radius:3px}
.footer-rule{position:absolute;left:0;top:236px;width:1200px;height:1px;background:#3a3a3a}
.copyright{position:absolute;left:0;width:1200px;top:251px;text-align:center;font-size:11px;color:#e0e0e0}
</style>
</head>
<body>

<header class="site-header">
  <div class="brand">Harrowfield Dentistry</div>
  <nav class="nav">
    <a class="active" href="#" style="left:509px">HOME</a>
    <a href="#" style="left:593px">SERVICES</a>
    <a href="#" style="left:699px">CONTACT US</a>
  </nav>
  <a class="btn-book" href="#" style="left:826px;top:24px;width:232px;height:41px">
    <svg viewBox="0 0 16 16" fill="none" stroke="#fff" stroke-width="1.5"><rect x="2" y="3" width="12" height="11" rx="1.5"/><path d="M2 6.5h12M5 1.5v3M11 1.5v3"/></svg>
    BOOK AN APPOINTMENT
  </a>
</header>

<section class="hero">
  <div class="abs" role="img" aria-label="Dentist examining a smiling patient reclining in a modern treatment chair" style="left:0;top:0;width:1200px;height:532px;background:linear-gradient(90deg,rgba(245,245,245,0.95) 0%,rgba(240,240,240,0.6) 40%,rgba(0,0,0,0) 60%)"></div>
  <h1 class="hero-title">Premium Dental Care for a Confident Smile</h1>
  <p class="hero-sub">Expert Cosmetic And Restorative Dentistry In A Luxurious Setting.</p>
  <a class="btn-book" href="#" style="left:141px;top:384px;width:233px;height:42px">
    <svg viewBox="0 0 16 16" fill="none" stroke="#fff" stroke-width="1.5"><rect x="2" y="3" width="12" height="11" rx="1.5"/><path d="M2 6.5h12M5 1.5v3M11 1.5v3"/></svg>
    BOOK AN APPOINTMENT
  </a>
</section>

<section class="services">
  <h2 class="section-title" style="top:41px">Our Dental <span>Services</span></h2>
  <p class="section-lead" style="top:86px">Comprehensive, high-quality care from cosmetic enhancements to emergency treatments—tailored to your smile.</p>

  <div class="service-card" style="left:141px;top:158px">
    <div class="service-icon"><svg viewBox="0 0 24 24"><circle cx="12" cy="12" r="9"/><path d="M8 14c1 1.5 2.3 2 4 2s3-.5 4-2"/><circle cx="9" cy="10" r=".6"/><circle cx="15" cy="10" r=".6"/></svg></div>
    <h3>Cosmetic Dentistry</h3>
    <p>Enhance your smile with treatments that improve tooth shape, color, and appearance.</p>
  </div>
  <div class="service-card" style="left:455px;top:158px">
    <div class="service-icon"><svg viewBox="0 0 24 24"><path d="M7 4c2-1 3.5 0 5 0s3-1 5 0c2 1 1.5 4 .5 6-.8 1.6-1.5 3-2 6-.3 2-2 2-2 0l-.5-3h-2l-.5 3c0 2-1.7 2-2 0-.5-3-1.2-4.4-2-6C5.5 8 5 5 7 4z"/><path d="M9 20h6"/></svg></div>
    <h3>Dental Implants</h3>
    <p>Permanent, natural-looking tooth replacements that restore function and confidence.</p>
  </div>
  <div class="service-card" style="left:767px;top:158px">
    <div class="service-icon"><svg viewBox="0 0 24 24"><path d="M5 5l14 14M19 5L5 19"/><circle cx="12" cy="12" r="2"/></svg></div>
    <h3>Emergency Services</h3>
    <p>Quick, professional treatment for dental emergencies, providing relief when you need it most.</p>
  </div>
  <div class="service-card" style="left:141px;top:368px">
    <div class="service-icon"><svg viewBox="0 0 24 24"><path d="M4 9c3 1 13 1 16 0-1 5-4 8-8 8s-7-3-8-8z"/><path d="M6 11.5h12M8 14h8"/></svg></div>
    <h3>Teeth Whitening</h3>
    <p>Brighten your smile with safe, professional whitening treatments that deliver fast, noticeable results.</p>
  </div>
  <div class="service-card" style="left:455px;top:368px">
    <div class="service-icon"><svg viewBox="0 0 24 24"><path d="M7 5c2-1 3.5 0 5 0s3-1 5 0c2 1 1.5 4 .5 6-.8 1.6-1.5 3-2 6-.3 2-2 2-2 0l-.5-3h-2l-.5 3c0 2-1.7 2-2 0-.5-3-1.2-4.4-2-6C5.5 9 5 6 7 5z"/><path d="M18 2v3M16.5 3.5h3"/></svg></div>
    <h3>Dental Hygiene</h3>
    <p>Preventive cleanings and exams to keep your teeth and gums healthy, fresh, and cavity-free.</p>
  </div>
  <div class="service-card" style="left:767px;top:368px">
    <div class="service-icon"><svg viewBox="0 0 24 24"><path d="M7 5c2-1 3.5 0 5 0s3-1 5 0c2 1 1.5 4 .5 6-.8 1.6-1.5 3-2 6-.3 2-2 2-2 0l-.5-3h-2l-.5 3c0 2-1.7 2-2 0-.5-3-1.2-4.4-2-6C5.5 9 5 6 7 5z"/><path d="M10 8l2 2 2-2"/></svg></div>
    <h3>Tooth Restoration</h3>
    <p>Repair and restore damaged teeth with natural-looking fillings, crowns, and bridges for a healthier smile.</p>
  </div>
</section>

<section class="why">
  <h2 class="section-title" style="top:60px">Why <span>Choose</span> Us?</h2>
  <p class="section-lead" style="top:105px">Experience expert care in a modern, comfort-first clinic—where advanced technology meets personalized treatment.</p>

  <div class="why-item" style="top:186px">
    <div class="why-icon"><svg viewBox="0 0 24 24"><path d="M3 5h18v14H3z M5 7v10h14V7z"/><path d="M9 9c1-.5 2 0 3 0s2-.5 3 0c1 .6.6 2.5 0 3.5-.4.8-.6 1.8-.9 3-.2.6-.9.6-1-.1l-.3-1.4h-1.6l-.3 1.4c-.1.7-.8.7-1 .1-.3-1.2-.5-2.2-.9-3C8.4 11.5 8 9.6 9 9z"/></svg></div>
    <h3>Board-Certified Dentists</h3>
    <p>Expertise you can trust, backed by advanced training and credentials.</p>
  </div>
  <div class="why-item" style="top:300px">
    <div class="why-icon"><svg viewBox="0 0 24 24"><path d="M6 5c2.5-1.2 4.3 0 6 0s3.5-1.2 6 0c2.4 1.2 1.8 5 .6 7.3-1 1.9-1.8 3.6-2.4 7.2-.4 2.4-2.4 2.4-2.4 0l-.6-3.6h-2.4l-.6 3.6c0 2.4-2 2.4-2.4 0-.6-3.6-1.4-5.3-2.4-7.2C4.2 10 3.6 6.2 6 5z"/></svg></div>
    <h3>Pain-Free Treatments</h3>
    <p>Gentle techniques and modern technology for a stress-free experience.</p>
  </div>
  <div class="why-item" style="top:413px">
    <div class="why-icon"><svg viewBox="0 0 24 24"><path d="M5 4h2l3 9h8a2 2 0 0 1 0 4h-3v3h3v1H9v-1h3v-3H9z"/><circle cx="16" cy="6" r="2"/></svg></div>
    <h3>Luxury, Comfort-First Clinic</h3>
    <p>Designed to help you relax—because your comfort matters.</p>
  </div>
  <div class="why-item" style="top:525px">
    <div class="why-icon"><svg viewBox="0 0 24 24"><path d="M3 8h16a2 2 0 0 1 2 2v9a2 2 0 0 1-2 2H5a2 2 0 0 1-2-2z"/><path d="M5 7l10-4 2 4z"/></svg></div>
    <h3>Flexible Payment Plans</h3>
    <p>Quality care made accessible with tailored financing options.</p>
  </div>

  <div class="portrait-frame"></div>
  <div class="portrait" role="img" aria-label="Smiling dentist in a white coat with arms crossed in a bright clinic"></div>
</section>

<section class="visit">
  <h2 class="section-title" style="top:70px">Visit Our <span>Clinic</span></h2>
  <p class="section-lead" style="top:115px;left:380px;width:440px">Located in the heart of Harrowfield, our clinic offers flexible hours and easy access to premium dental care.</p>
  <div class="map-area" role="img" aria-label="Street map showing the clinic location"></div>
  <div class="info-card">
    <h4 style="top:28px"><svg viewBox="0 0 24 24"><path d="M12 22s7-7 7-12a7 7 0 0 0-14 0c0 5 7 12 7 12z"/><circle cx="12" cy="10" r="2.5"/></svg>Visit Us</h4>
    <p style="top:62px">48 Larchmere Lane, Harrowfield</p>
    <h4 style="top:96px"><svg viewBox="0 0 24 24"><circle cx="12" cy="12" r="9"/><path d="M12 7v5l3 2"/></svg>Operating Hours</h4>
    <p style="top:131px">Mon–Fri: 8:00 AM – 6:00 PM<br>Sat: 9:00 AM – 2:00 PM<br>Closed Sundays</p>
    <h4 style="top:196px"><svg viewBox="0 0 24 24"><path d="M5 3h4l2 5-2.5 1.5a11 11 0 0 0 6 6L16 13l5 2v4a2 2 0 0 1-2 2A16 16 0 0 1 3 5a2 2 0 0 1 2-2z"/></svg>Call Us</h4>
    <p style="top:231px">(555) 014-2290</p>
    <a class="btn-call" href="#">Call Now</a>
  </div>
</section>

<section class="reviews">
  <h2 class="section-title" style="top:60px">What Our <span>Patients Say</span></h2>
  <p class="section-lead" style="top:105px">Real stories from patients who've experienced compassionate care, outstanding results, and a confident new smile.</p>

  <div class="arrow-btn" style="left:91px;border:1.5px solid #fff"><svg viewBox="0 0 14 14" stroke="#fff"><path d="M9 2L4 7l5 5"/></svg></div>

  <div class="review-card" style="left:141px">
    <div class="stars">
      <svg viewBox="0 0 24 24"><path d="M12 2l3 6.5 7 .8-5.2 4.8 1.4 7L12 17.6 5.8 21l1.4-7L2 9.3l7-.8z"/></svg>
      <svg viewBox="0 0 24 24"><path d="M12 2l3 6.5 7 .8-5.2 4.8 1.4 7L12 17.6 5.8 21l1.4-7L2 9.3l7-.8z"/></svg>
      <svg viewBox="0 0 24 24"><path d="M12 2l3 6.5 7 .8-5.2 4.8 1.4 7L12 17.6 5.8 21l1.4-7L2 9.3l7-.8z"/></svg>
      <svg viewBox="0 0 24 24"><path d="M12 2l3 6.5 7 .8-5.2 4.8 1.4 7L12 17.6 5.8 21l1.4-7L2 9.3l7-.8z"/></svg>
      <svg viewBox="0 0 24 24"><path d="M12 2l3 6.5 7 .8-5.2 4.8 1.4 7L12 17.6 5.8 21l1.4-7L2 9.3l7-.8z"/></svg>
    </div>
    <div class="review-date">10th Feb, 2023</div>
    <p class="review-text">"The team made me feel comfortable from the moment I walked in. My smile has never looked better!"</p>
    <div class="avatar" role="img" aria-label="Patient portrait"></div>
    <div class="reviewer">Owen T.</div>
    <div class="role">Customer</div>
  </div>

  <div class="review-card" style="left:611px">
    <div class="stars">
      <svg viewBox="0 0 24 24"><path d="M12 2l3 6.5 7 .8-5.2 4.8 1.4 7L12 17.6 5.8 21l1.4-7L2 9.3l7-.8z"/></svg>
      <svg viewBox="0 0 24 24"><path d="M12 2l3 6.5 7 .8-5.2 4.8 1.4 7L12 17.6 5.8 21l1.4-7L2 9.3l7-.8z"/></svg>
      <svg viewBox="0 0 24 24"><path d="M12 2l3 6.5 7 .8-5.2 4.8 1.4 7L12 17.6 5.8 21l1.4-7L2 9.3l7-.8z"/></svg>
      <svg viewBox="0 0 24 24"><path d="M12 2l3 6.5 7 .8-5.2 4.8 1.4 7L12 17.6 5.8 21l1.4-7L2 9.3l7-.8z"/></svg>
      <svg viewBox="0 0 24 24"><path d="M12 2l3 6.5 7 .8-5.2 4.8 1.4 7L12 17.6 5.8 21l1.4-7L2 9.3l7-.8z"/></svg>
    </div>
    <div class="review-date">06th Feb, 2023</div>
    <p class="review-text">"Beautiful clinic, friendly staff, and pain-free treatment. Truly a premium dental experience."</p>
    <div class="avatar" role="img" aria-label="Patient portrait" style="background:linear-gradient(135deg,#f2cf6a,#c99a4a)"></div>
    <div class="reviewer">Lena R.</div>
    <div class="role">Customer</div>
  </div>

  <div class="arrow-btn" style="left:1079px;background:#fff"><svg viewBox="0 0 14 14" stroke="#2d3e50"><path d="M5 2l5 5-5 5"/></svg></div>

  <a class="btn-view" href="#">View All</a>
</section>

<footer class="site-footer">
  <div class="footer-brand">Harrowfield Dentistry</div>
  <nav class="footer-nav"><a href="#">Home</a><a href="#">Our Services</a><a href="#">Contact Us</a></nav>
  <div class="social"><span></span><span></span><span></span></div>
  <div class="footer-rule"></div>
  <div class="copyright">© 2025 Harrowfield dentistry. All Rights Reserved.</div>
</footer>

</body>
</html>
```